Modern and professional facebook ad for disability service

Design a facebook ad for a disability service. Want something bright and fun and eyecatching. Would ideally like a carousel ad as this will give us more options to provide information.
CONTENT:
- Looking for a Plan Manager who will support your QWTR journey so that you can focus on living your best possible life and achieve your QWTR Goals?
- Then join the Wattlebrook Plan Management family today - quick and easy sign up.
- Friendly, Reliable, Responsive Service
- Dedicate Plan Managers so you always speak to the same person
- Fast Payment of Provider Invoices
- Supporting you to live Your Life, Your Way
- Call us today on 1300 482 316
- www.wattlebrookplanmanagement.com.au
Updates

Sick

Target Market(s)

Disability Sector

Font styles to use
Other font styles liked:
• Raleway

Requirements
Must have
• Bright colours and eye catching design

```html
<!DOCTYPE html>
<html lang="en">
<head>
<meta charset="utf-8">
<title>Wattlebrook Plan Management – Carousel Ad</title>
<link rel="stylesheet" href="https://fonts.googleapis.com/css2?family=Libre+Baskerville:wght@700&family=Poppins:wght@500;700&family=Sacramento&display=swap">
<style>
  :root {
    --canvas: #c5dfe0;
    --magenta: #a8326b;
    --teal: #10807f;
    --purple: #4b2d7f;
    --white: #ffffff;
    --photo-warm: #d9b8a0;
    --photo-cool: #6fa9ab;
  }
  * { margin: 0; padding: 0; box-sizing: border-box; }
  html, body { width: 1200px; height: 600px; overflow: hidden; background: var(--canvas); }
  .carousel {
    position: absolute; top: 201px; left: 0;
    width: 1200px; height: 198px;
    display: flex;
  }
  .spread { width: 400px; height: 198px; display: block; }
  .bg { fill: var(--magenta); }
  .wave { fill: var(--teal); }
  .wave-line, .photo-ring { fill: none; stroke: var(--white); stroke-width: 4; }
  .ring-dot { fill: var(--white); }
  .headline { font-family: "Libre Baskerville", Georgia, serif; font-weight: 700; fill: var(--white); }
  .headline--lg { font-size: 27px; }
  .headline--sm { font-size: 18px; }
  .script { font-family: "Sacramento", cursive; fill: var(--white); }
  .script--lg { font-size: 52px; }
  .script--sm { font-size: 36px; }
  .cta-label { font-family: "Poppins", Arial, sans-serif; font-weight: 500; font-size: 20px; fill: var(--white); }
  .cta-phone { font-family: "Poppins", Arial, sans-serif; font-weight: 700; font-size: 28px; fill: var(--white); }
  .cta-pill { fill: var(--white); }
  .cta-url-box { fill: var(--magenta); }
  .cta-pill-text { font-family: "Poppins", Arial, sans-serif; font-weight: 700; font-size: 10px; fill: var(--teal); }
  .cta-url-text { font-family: "Poppins", Arial, sans-serif; font-weight: 500; font-size: 6.5px; fill: var(--white); }
  .brand-dot { fill: var(--purple); stroke: var(--white); stroke-width: 2; }
  .brand-name { font-family: "Libre Baskerville", Georgia, serif; font-weight: 700; font-size: 22px; fill: var(--white); }
  .phone-icon { fill: none; stroke: var(--white); stroke-width: 2.5; }
</style>
</head>
<body>
<main class="carousel">

  <!-- Spread 1 -->
  <svg class="spread" viewBox="0 0 828 410" xmlns="http://www.w3.org/2000/svg">
    <defs>
      <linearGradient id="photo-office" x1="0" y1="0" x2="1" y2="1">
        <stop offset="0" stop-color="#8fa7a6"/>
        <stop offset="1" stop-color="#d6c2ad"/>
      </linearGradient>
    </defs>
    <rect class="bg" width="828" height="410"/>
    <path class="wave" d="M0,285 C120,270 220,300 300,345 C380,390 520,350 620,310 C700,280 770,270 828,285 L828,410 L0,410Z"/>
    <path class="wave-line" d="M0,275 C120,260 220,290 300,335 C380,380 520,340 620,300 C700,270 770,260 828,275"/>
    <path role="img" aria-label="Photo of two women laughing together at an office table" fill="url(#photo-office)" d="M300,80 C360,40 470,30 540,60 C600,90 600,200 590,260 C575,340 500,390 420,385 C330,380 270,330 250,250 C235,180 250,110 300,80Z"/>
    <path class="photo-ring" d="M290,55 C360,10 490,5 560,45 C625,85 625,205 612,270 C595,355 505,408 420,405 C320,402 250,345 228,255 C212,180 230,95 290,55Z"/>
    <circle class="ring-dot" cx="228" cy="255" r="6"/><circle class="ring-dot" cx="375" cy="392" r="6"/><circle class="ring-dot" cx="612" cy="270" r="6"/><circle class="ring-dot" cx="250" cy="325" r="6"/>

    <text class="headline headline--sm" x="25" y="32">
      <tspan x="25">Looking for a</tspan>
      <tspan x="25" dy="21">Plan Manager</tspan>
      <tspan x="25" dy="21">who will support</tspan>
      <tspan x="25" dy="21">your QWTR journey</tspan>
      <tspan x="25" dy="21">so that you can focus</tspan>
      <tspan x="25" dy="21">on living your best</tspan>
      <tspan x="25" dy="21">possible life and</tspan>
      <tspan x="25" dy="21">achieve your QWTR</tspan>
      <tspan x="25" dy="21">Goals?</tspan>
    </text>
    <text class="headline headline--lg" text-anchor="end" x="805" y="40">
      <tspan x="805">Then join the</tspan>
      <tspan x="805" dy="32">Wattlebrook Plan</tspan>
      <tspan x="805" dy="32">Management</tspan>
      <tspan x="805" dy="32">family today</tspan>
    </text>
    <text class="script script--sm" text-anchor="end" x="805" y="170">
      <tspan x="805">Quick and</tspan>
      <tspan x="805" dy="34">Easy Sign Up</tspan>
    </text>

    <g class="brand">
      <circle class="brand-dot" cx="42" cy="357" r="14"/>
      <text class="brand-name" x="64" y="365">QWTR</text>
    </g>
    <g class="cta">
      <text class="cta-label" text-anchor="end" x="805" y="348">Call us today on</text>
      <path class="phone-icon" d="M630,365 a10,10 0 1,0 0.1,0Z"/>
      <text class="cta-phone" text-anchor="end" x="805" y="376">1300 482 316</text>
      <rect class="cta-pill" x="622" y="382" width="74" height="18"/>
      <text class="cta-pill-text" x="628" y="395">Visit Our Site</text>
      <rect class="cta-url-box" x="696" y="382" width="109" height="18"/>
      <text class="cta-url-text" x="699" y="393.5">www.wattlebrookplanmanagement.com.au</text>
    </g>
  </svg>

  <!-- Spread 2 -->
  <svg class="spread" viewBox="0 0 828 410" xmlns="http://www.w3.org/2000/svg">
    <defs>
      <linearGradient id="photo-laptop" x1="0" y1="0" x2="1" y2="1">
        <stop offset="0" stop-color="#5fa3a3"/>
        <stop offset="1" stop-color="#e3cbb6"/>
      </linearGradient>
    </defs>
    <rect class="bg" width="828" height="410"/>
    <path class="wave" d="M0,285 C120,270 220,300 300,345 C380,390 520,350 620,310 C700,280 770,270 828,285 L828,410 L0,410Z"/>
    <path class="wave-line" d="M0,275 C120,260 220,290 300,335 C380,380 520,340 620,300 C700,270 770,260 828,275"/>
    <path role="img" aria-label="Photo of two young women smiling while using a laptop" fill="url(#photo-laptop)" d="M300,80 C360,40 470,30 540,60 C600,90 600,200 590,260 C575,340 500,390 420,385 C330,380 270,330 250,250 C235,180 250,110 300,80Z"/>
    <path class="photo-ring" d="M290,55 C360,10 490,5 560,45 C625,85 625,205 612,270 C595,355 505,408 420,405 C320,402 250,345 228,255 C212,180 230,95 290,55Z"/>
    <circle class="ring-dot" cx="228" cy="155" r="6"/><circle class="ring-dot" cx="375" cy="392" r="6"/><circle class="ring-dot" cx="612" cy="122" r="6"/><circle class="ring-dot" cx="550" cy="305" r="6"/>

    <text class="headline headline--lg" x="25" y="40">
      <tspan x="25">Dedicate Plan</tspan>
      <tspan x="25" dy="33">Managers so</tspan>
      <tspan x="25" dy="33">you always</tspan>
      <tspan x="25" dy="33">speak to the</tspan>
    </text>
    <text class="script script--lg" x="25" y="180">
      <tspan x="25">Same</tspan>
      <tspan x="25" dy="55">Person</tspan>
    </text>
    <text class="headline headline--lg" text-anchor="end" x="805" y="40">
      <tspan x="805">Friendly,</tspan>
      <tspan x="805" dy="35">Reliable,</tspan>
      <tspan x="805" dy="35">Responsive</tspan>
    </text>
    <text class="script script--lg" text-anchor="end" x="805" y="170">Service</text>

    <g class="brand">
      <circle class="brand-dot" cx="42" cy="357" r="14"/>
      <text class="brand-name" x="64" y="365">QWTR</text>
    </g>
    <g class="cta">
      <text class="cta-label" text-anchor="end" x="805" y="348">Call us today on</text>
      <path class="phone-icon" d="M630,365 a10,10 0 1,0 0.1,0Z"/>
      <text class="cta-phone" text-anchor="end" x="805" y="376">1300 482 316</text>
      <rect class="cta-pill" x="622" y="382" width="74" height="18"/>
      <text class="cta-pill-text" x="628" y="395">Visit Our Site</text>
      <rect class="cta-url-box" x="696" y="382" width="109" height="18"/>
      <text class="cta-url-text" x="699" y="393.5">www.wattlebrookplanmanagement.com.au</text>
    </g>
  </svg>

  <!-- Spread 3 -->
  <svg class="spread" viewBox="0 0 828 410" xmlns="http://www.w3.org/2000/svg">
    <defs>
      <linearGradient id="photo-support" x1="0" y1="0" x2="1" y2="1">
        <stop offset="0" stop-color="#b9bcbc"/>
        <stop offset="1" stop-color="#d8b563"/>
      </linearGradient>
    </defs>
    <rect class="bg" width="828" height="410"/>
    <path class="wave" d="M0,285 C120,270 220,300 300,345 C380,390 520,350 620,310 C700,280 770,270 828,285 L828,410 L0,410Z"/>
    <path class="wave-line" d="M0,275 C120,260 220,290 300,335 C380,380 520,340 620,300 C700,270 770,260 828,275"/>
    <path role="img" aria-label="Photo of a support worker helping an older woman in a wheelchair use a laptop" fill="url(#photo-support)" d="M300,80 C360,40 470,30 540,60 C600,90 600,200 590,260 C575,340 500,390 420,385 C330,380 270,330 250,250 C235,180 250,110 300,80Z"/>
    <path class="photo-ring" d="M290,55 C360,10 490,5 560,45 C625,85 625,205 612,270 C595,355 505,408 420,405 C320,402 250,345 228,255 C212,180 230,95 290,55Z"/>
    <circle class="ring-dot" cx="228" cy="155" r="6"/><circle class="ring-dot" cx="375" cy="392" r="6"/><circle class="ring-dot" cx="612" cy="122" r="6"/><circle class="ring-dot" cx="248" cy="315" r="6"/>

    <text class="headline headline--lg" x="25" y="42">
      <tspan x="25">Fast</tspan>
      <tspan x="25" dy="38">Payment of</tspan>
      <tspan x="25" dy="38">Provider</tspan>
    </text>
    <text class="script script--lg" x="25" y="178">Invoices</text>
    <text class="headline headline--lg" text-anchor="end" x="805" y="42">
      <tspan x="805">Supporting</tspan>
      <tspan x="805" dy="38">you to live</tspan>
      <tspan x="805" dy="38">Your Life,</tspan>
    </text>
    <text class="script script--lg" text-anchor="end" x="805" y="172">Your Way</text>

    <g class="brand">
      <circle class="brand-dot" cx="42" cy="357" r="14"/>
      <text class="brand-name" x="64" y="365">QWTR</text>
    </g>
    <g class="cta">
      <text class="cta-label" text-anchor="end" x="805" y="348">Call us today on</text>
      <path class="phone-icon" d="M630,365 a10,10 0 1,0 0.1,0Z"/>
      <text class="cta-phone" text-anchor="end" x="805" y="376">1300 482 316</text>
      <rect class="cta-pill" x="622" y="382" width="74" height="18"/>
      <text class="cta-pill-text" x="628" y="395">Visit Our Site</text>
      <rect class="cta-url-box" x="696" y="382" width="109" height="18"/>
      <text class="cta-url-text" x="699" y="393.5">www.wattlebrookplanmanagement.com.au</text>
    </g>
  </svg>

</main>
</body>
</html>
```